Brightfield Grove LLC business card

I created a front and back idea of what I want. Also I included my Brightfield Grove logo to be used on the card. Please use your creativity to make it look professional and awesome! Use the all text and phrases in the sample card that I made.

(Front of card)Key words and phrases:
FOOD GROWING MACHINES
Aeroponics Technology
No soil
No pesticides
98% less water
Grow year round

(Back of card)
EVERY MONTH ONE SPIRE PLANTER WILL BE GIVEN AWAY
FOLLOW US ON IG FOR A CHANCE TO WIN A SPIRE PLANTER
FOOD GROWING MACHINES
Vertical Farming
Urban Farming
100% Organic
Grows 40% Faster
Indoors/outdoors

My contact info:
Chef Rolo
Phone:415 637-2094
web: brightfieldgrove.example
IG: brightfieldgrovex

Target Market(s)

urban farming, vertical farming gardening

Industry/Entity Type

Gardening

Contact Information for Business Card

Front of card)Key words and phrases:
FOOD GROWING MACHINES
Aeroponics Technology
No soil
No pesticides
98% less water
Grow year round

(Back of card)
FOOD GROWING MACHINES
Vertical Farming
Urban Farming
100% Organic
Grows 40% Faster
Indoors/outdoors

My contact info:
Phone:415 637-2094
web: brightfieldgrove.example
IG: brightfieldgrovex

Requirements
Must have
• My contact info:
Chef Rolo
Phone:415 637-2094
web: brightfieldgrove.example
IG: brightfieldgrovex
Nice to have
• Great imagery and easy to read. Try to incorporate the image that I uploaded of the little girl.

```html
<!DOCTYPE html>
<html lang="en">
<head>
<meta charset="utf-8">
<title>Brightfield Grove – Business Card</title>
<link href="https://fonts.googleapis.com/css2?family=Roboto:wght@400;500;700&display=swap" rel="stylesheet">
<style>
  :root{
    --stage:#272727;
    --lime:#8cff00;
    --blue:#5271ff;
    --forest:#2f8a16;
    --ink:#1b3a0a;
    --white:#ffffff;
  }
  *{margin:0;padding:0;box-sizing:border-box}
  html,body{width:1200px;height:801px;overflow:hidden;background:var(--stage);font-family:"Roboto",Arial,sans-serif}
  .card{position:absolute;top:274px;width:443px;height:263px;overflow:hidden;box-shadow:3px 3px 4px rgba(0,0,0,.6)}

  /* Info side */
  .card--info{left:153px;background:var(--blue)}
  .info__banner{position:absolute;left:0;top:0;width:100%;height:45px;background:var(--lime)}
  .info__banner p{position:absolute;left:23px;top:17px;font-weight:500;font-size:12.6px;color:var(--forest);white-space:nowrap}
  .info__footer{position:absolute;left:0;bottom:0;width:100%;height:8px;background:var(--lime)}
  .info__promo{position:absolute;left:23px;top:82px;color:var(--lime);font-weight:500;font-size:12.6px;line-height:15.5px}
  .info__tagline{position:absolute;left:23px;top:121px;color:var(--lime);font-weight:500;font-size:12.6px}
  .info__features{position:absolute;left:23px;top:163px;list-style:none;color:var(--white);font-size:12.8px;line-height:15.7px}
  .info__features li{position:relative;padding-left:10.5px}
  .info__features li::before{content:"";position:absolute;left:0;top:5px;width:5px;height:5px;border-radius:50%;background:var(--lime)}
  .brand{position:absolute;right:20px;top:84px;width:150px;text-align:right;color:var(--lime);font-weight:700;font-size:22px;line-height:22px}
  .contact__name{position:absolute;right:27px;top:164px;color:var(--lime);font-weight:500;font-size:16px}
  .contact__list{position:absolute;right:23px;top:195px;list-style:none;color:var(--white);font-size:12.8px;line-height:15.7px;text-align:right}
  .contact__list li{display:flex;justify-content:flex-end;align-items:center;gap:4px}
  .contact__list svg{width:11px;height:11px;flex:none}

  /* Feature side */
  .card--feature{left:625px;background:var(--lime)}
  .feature__photo{position:absolute;left:0;top:0;width:100%;height:226px;
    background:linear-gradient(90deg,#5a4a3a 0%,#8d7868 25%,#d8438a 40%,#c9c2b8 55%,#5f9a3a 70%,#3f7a22 100%)}
  .feature__banner{position:absolute;left:0;top:0;width:100%;height:31px;background:rgba(110,190,0,.82)}
  .feature__title{position:absolute;left:0;top:4px;width:100%;text-align:center;color:var(--white);font-weight:500;font-size:19.4px;letter-spacing:.1px}
  .feature__subtitle{position:absolute;left:0;top:32px;width:100%;padding-left:14px;text-align:center;color:var(--white);font-weight:700;font-size:14px}
  .feature__benefits{position:absolute;left:0;top:226px;width:100%;height:37px;background:var(--lime);list-style:none;font-weight:500;font-size:13px;color:var(--ink)}
  .feature__benefits li{position:absolute;top:11px;white-space:nowrap}
</style>
</head>
<body>

<section class="card card--info">
  <div class="info__banner"><p>EVERY MONTH ONE SPIRE PLANTER WILL BE GIVEN AWAY</p></div>
  <p class="info__promo">FOLLOW US ON IG FOR A CHANCE<br>TO WIN A SPIRE PLANTER</p>
  <p class="info__tagline">FOOD GROWING MACHINES</p>
  <ul class="info__features">
    <li>Vertical Farming</li>
    <li>Urban Farming</li>
    <li>100% Organic</li>
    <li>Grows 40% Faster</li>
    <li>Indoors/outdoors</li>
  </ul>
  <p class="brand">BRIGHTFIELD GROVE</p>
  <p class="contact__name">CHEF ROLO</p>
  <ul class="contact__list">
    <li>415 637-2094
      <svg viewBox="0 0 12 12" aria-hidden="true"><path d="M3 1.2 4.6 3.4 3.6 4.6c.6 1.5 2 2.9 3.6 3.6l1.2-1 2.2 1.6-.8 1.8C5.5 10.4 1.6 6.5 1.2 2z" fill="none" stroke="#8cff00" stroke-width="1.1" stroke-linejoin="round"/></svg>
    </li>
    <li>www.brightfieldgrove.example
      <svg viewBox="0 0 12 12" aria-hidden="true"><g fill="none" stroke="#8cff00" stroke-width="1"><circle cx="6" cy="6" r="5"/><ellipse cx="6" cy="6" rx="2.2" ry="5"/><path d="M1 6h10M2 3.3h8M2 8.7h8"/></g></svg>
    </li>
    <li>brightfieldgrovex
      <svg viewBox="0 0 12 12" aria-hidden="true"><circle cx="6" cy="6" r="5" fill="none" stroke="#8cff00" stroke-width="1.2"/></svg>
    </li>
  </ul>
  <div class="info__footer"></div>
</section>

<section class="card card--feature">
  <div class="feature__photo" role="img" aria-label="Photo of a young girl in a pink shirt holding a colander beside a leafy spire planter of chard in a kitchen"></div>
  <div class="feature__banner"></div>
  <h1 class="feature__title">FOOD GROWING MACHINES</h1>
  <p class="feature__subtitle">Aeroponics Technology</p>
  <ul class="feature__benefits">
    <li style="left:34px">No soil</li>
    <li style="left:92px">No pesticides</li>
    <li style="left:192px">98% less water</li>
    <li style="left:304px">Grow year round</li>
  </ul>
</section>

</body>
</html>
```